Varnik Holdings — Business Card Design Brief
Overview
Design a double-sided business card for Varnik Holdings that highlights our two service arms: Varnik Communications (telecommunications) and Varnik Energy (business energy solutions). The card should feel smart and stand out when handed to clients.

Objectives
Showcase our areas of specialty clearly.
Reflect the overall Varnik / Varnik Holdings brand while acknowledging both arms.
Explore using both logos (Communications + Energy) or one unified logo, depending on the design.

Deliverables
One double-sided business card design (front + back).

Content & Copy
Front (preferred): Logo: Varnik / Varnik Holdings
Descriptor: Business Communications | Business Energy
Back:My contact details and company details
Core products: Business Mobile • Telephony • Internet • Business Energy Solutions

Brand & Visual Direction
We have a group logo currently tailored more toward telecoms, plus a separate Varnik Energy logo.
Please explore layouts that use both logos or just one, whichever works best.
Color: I wouldn't mind seeing an option using our the Blue/Purple gradient from our website (varnik-example.co.uk), but also open to non-gradient approaches and other colours..

Overall look: Smart, modern, and distinctive.
Format & Print Specs
Double-sided business card format. (Use a standard size

Must-Haves
Front: Varnik wording or Varnik Holdings wording with atleast 1 logo also on front “Business Communications | Business Energy.”

Back: Contact + company details and core products.
A design that stands out while remaining professional.

Nice-to-Have Options
A gradient version using our site’s Blue/Purple gradient.
A non-gradient version.
A dual-logo treatment versus a single-logo treatment.

Thanks
Owen

```html
<!DOCTYPE html>
<html lang="en">
<head>
<meta charset="utf-8">
<title>Varnik Holdings – Business Card</title>
<link rel="stylesheet" href="https://fonts.googleapis.com/css2?family=Montserrat:wght@500;600;700&family=Poppins:wght@700&family=Tinos&display=swap">
<style>
  :root {
    --stage: #9a9a9a;
    --card: #ffffff;
    --navy: #1c1464;
    --green: #46ac0a;
    --lime: #c6d20a;
    --ink: #1a1a1a;
    --rule: #2a2a2a;
  }
  * { box-sizing: border-box; margin: 0; padding: 0; }
  html, body { width: 1200px; height: 1059px; overflow: hidden; }
  body { background: var(--stage); position: relative; font-family: "Montserrat", sans-serif; }

  .card { position: absolute; border-radius: 24px; overflow: hidden; box-shadow: 0 14px 28px rgba(0,0,0,.35); }

  .card-front { left: 252px; top: 88px; width: 724px; height: 415px; background: var(--card); }
  .brand-mark { position: absolute; left: 440px; top: 30px; width: 230px; text-align: center; }
  .brand-mark .dot { display: block; width: 84px; height: 84px; margin: 0 auto 14px; border-radius: 50%; background: var(--green); }
  .brand-mark .name { font-weight: 700; font-size: 42px; letter-spacing: 1px; color: var(--navy); line-height: 1; }

  .holder { position: absolute; left: 41px; top: 157px; }
  .holder-name { font-weight: 700; font-size: 28px; color: var(--navy); line-height: 1.1; }
  .holder-role { font-family: "Tinos", serif; font-size: 18px; color: var(--ink); margin-top: 8px; }
  .divider { position: absolute; left: 41px; top: 236px; width: 634px; height: 1px; background: var(--rule); }

  .contacts { position: absolute; left: 38px; top: 254px; list-style: none; }
  .contacts li { display: flex; align-items: center; height: 34px; font-weight: 500; font-size: 19px; color: var(--ink); }
  .contacts li.address { margin-top: 2px; }
  .contacts svg { width: 20px; height: 20px; margin-right: 12px; flex: none; fill: var(--green); }

  .services { position: absolute; right: 49px; top: 256px; text-align: right; list-style: none; }
  .services li { font-weight: 700; font-size: 19px; color: var(--navy); line-height: 28px; }

  .base-band { position: absolute; left: 0; bottom: 0; width: 724px; height: 12px; }

  .card-back { left: 253px; top: 566px; width: 712px; height: 407px; background: var(--navy); text-align: center; }
  .group-title { position: absolute; left: 0; right: 0; top: 40px; padding-left: 38px; font-family: "Poppins", sans-serif; font-weight: 700; font-size: 52px; color: #fff; line-height: 1; }
  .descriptor { position: absolute; left: 0; right: 0; top: 104px; padding-left: 38px; font-weight: 600; font-size: 17px; letter-spacing: .5px; color: var(--lime); line-height: 1; }
  .back-mark .dot { position: absolute; left: 283px; top: 144px; width: 140px; height: 140px; border-radius: 50%; background: var(--green); }
  .back-mark .name { position: absolute; left: 0; right: 0; top: 300px; font-weight: 700; font-size: 64px; letter-spacing: 1px; color: #fff; line-height: 1; }
</style>
</head>
<body>

<section class="card card-front" aria-label="Business card front">
  <div class="brand-mark">
    <span class="dot"></span>
    <div class="name">VARNIK</div>
  </div>

  <div class="holder">
    <h1 class="holder-name">Daniel Archer</h1>
    <p class="holder-role">Owner</p>
  </div>
  <div class="divider"></div>

  <ul class="contacts">
    <li><svg viewBox="0 0 24 24" aria-hidden="true"><path d="M6.6 10.8a15.1 15.1 0 0 0 6.6 6.6l2.2-2.2a1 1 0 0 1 1-.25 11.4 11.4 0 0 0 3.6.6 1 1 0 0 1 1 1V20a1 1 0 0 1-1 1A17 17 0 0 1 3 4a1 1 0 0 1 1-1h3.5a1 1 0 0 1 1 1c0 1.25.2 2.45.6 3.6a1 1 0 0 1-.25 1z"/></svg>044-555 010 203</li>
    <li><svg viewBox="0 0 24 24" aria-hidden="true"><path d="M2 5h20v14H2z M2 5l10 7 10-7" /></svg>hello@varnik-example.co.uk</li>
    <li><svg viewBox="0 0 24 24" aria-hidden="true"><circle cx="12" cy="12" r="10"/></svg>www.varnik-example.co.uk</li>
    <li class="address"><svg viewBox="0 0 24 24" aria-hidden="true"><path d="M12 2a7 7 0 0 0-7 7c0 5.2 7 13 7 13s7-7.8 7-13a7 7 0 0 0-7-7zm0 9.5A2.5 2.5 0 1 1 12 6.5a2.5 2.5 0 0 1 0 5z"/></svg>18 Harrow Lane, Leeds LS1 4AB, United Kingdom</li>
  </ul>

  <ul class="services">
    <li>• Business Mobile</li>
    <li>• Telephony • Internet</li>
    <li>• Business Energy Solutions</li>
  </ul>

  <svg class="base-band" viewBox="0 0 724 12" preserveAspectRatio="none" aria-hidden="true">
    <polygon points="0,0 358,0 363,12 0,12" fill="var(--navy)"/>
    <polygon points="362,0 724,0 724,12 367,12" fill="var(--green)"/>
  </svg>
</section>

<section class="card card-back" aria-label="Business card back">
  <h2 class="group-title">Varnik Holdings</h2>
  <p class="descriptor">Business Communications | Business Energy</p>
  <div class="back-mark">
    <span class="dot"></span>
    <div class="name">VARNIK</div>
  </div>
</section>

</body>
</html>
```